Business Card Design

New business card design

Target Market(s)

Residential & Commercial Property Managers

Industry/Entity Type

Plumbing Services

Contact Information for Business Card

Name - Rowan Keddle, title - Director, Phone Number - 0431 286 517, email - rowan@tbk-plumbing.com.au, Company ABN - 73 215 904 386,

Font styles to use
Sans Serif

Colors
0054AA
0677BA
7BADD7
CADEEF
E8F1F8

```html
<!DOCTYPE html>
<html lang="en">
<head>
<meta charset="utf-8">
<title>TBK Plumbing Services – Business Card</title>
<link rel="stylesheet" href="https://fonts.googleapis.com/css2?family=Poppins:wght@300;400;500;600&display=swap">
<style>
  :root {
    --page: #e9e6e1;
    --card: #efe7dc;
    --ink: #2a2c2e;
    --ink-soft: #5e5650;
    --teal: #1a8aa2;
    --teal-deep: #117a92;
    --brown: #6b5e55;
    --cream: #f3ece2;
  }
  * { box-sizing: border-box; margin: 0; padding: 0; }
  html, body {
    width: 1200px; height: 1046px; overflow: hidden;
    background: var(--page);
    font-family: "Poppins", sans-serif;
  }
  .card {
    position: absolute; left: 50px; top: 222px;
    width: 1100px; height: 601px;
    border-radius: 30px; overflow: hidden;
    background: var(--card);
    box-shadow: 0 10px 30px rgba(0,0,0,0.12);
  }
  .card-art { position: absolute; inset: 0; }
  .brand { position: absolute; left: 44px; top: 22px; }
  .brand-name {
    font-weight: 500; font-size: 118px; line-height: 1;
    color: var(--ink); letter-spacing: 2px;
  }
  .brand-tagline {
    margin-top: 34px; font-size: 17px; font-weight: 400;
    color: var(--ink-soft); letter-spacing: 20.5px; padding-left: 22px;
  }
  .person { position: absolute; right: 48px; top: 52px; text-align: right; }
  .person-name { font-size: 48px; line-height: 1.1; color: var(--brown); font-weight: 400; }
  .person-name .first { color: var(--teal); font-weight: 600; }
  .person-title { font-size: 24px; font-weight: 500; color: var(--ink); margin-top: 8px; }
  .accent-bar {
    position: absolute; right: 0; top: 58px;
    width: 32px; height: 86px; background: var(--brown);
  }
  .contacts { position: absolute; left: 36px; top: 382px; list-style: none; }
  .contacts li {
    display: flex; align-items: center; gap: 16px;
    height: 34px; font-size: 24px; color: var(--ink);
  }
  .contacts svg { width: 22px; height: 22px; flex: none; }
  .abn {
    position: absolute; right: 48px; top: 534px;
    font-size: 22px; color: var(--cream); letter-spacing: 0.5px;
  }
</style>
</head>
<body>
  <section class="card">
    <svg class="card-art" viewBox="0 0 1100 601" aria-hidden="true">
      <path d="M0,520 C150,600 350,612 560,578 C760,545 880,442 965,410 C1015,394 1060,392 1100,398 L1100,601 L0,601 Z" fill="var(--teal)"/>
      <path d="M0,470 C80,545 250,585 425,572" fill="none" stroke="var(--cream)" stroke-width="12"/>
      <path d="M0,466 C80,540 250,580 425,568" fill="none" stroke="var(--brown)" stroke-width="7"/>
    </svg>

    <div class="brand">
      <div class="brand-name">tbk</div>
      <div class="brand-tagline">plumbing services</div>
    </div>

    <div class="person">
      <div class="person-name"><span class="first">Rowan</span> Keddle</div>
      <div class="person-title">Director</div>
    </div>
    <div class="accent-bar"></div>

    <ul class="contacts">
      <li>
        <svg viewBox="0 0 24 24"><path d="M6.6 2.5l3 3.2-1.9 2.4c1.2 2.8 3.4 5 6.2 6.2l2.4-1.9 3.2 3-2 3.6C10.6 18.6 5.4 13.4 3 6.5z" fill="var(--teal)"/><path d="M14 3a7 7 0 0 1 7 7M14 6.5a3.5 3.5 0 0 1 3.5 3.5" fill="none" stroke="var(--teal)" stroke-width="1.8" stroke-linecap="round"/></svg>
        0431 286 517
      </li>
      <li>
        <svg viewBox="0 0 24 24"><rect x="2" y="6" width="20" height="15" rx="1.5" fill="var(--teal)"/><path d="M2 7l10 8 10-8" fill="none" stroke="var(--cream)" stroke-width="1.6"/></svg>
        www.tbk-plumbing.com.au
      </li>
      <li>
        <svg viewBox="0 0 24 24"><circle cx="12" cy="12" r="10" fill="var(--teal)"/><path d="M2 12h20M12 2c3 3 3 17 0 20M12 2c-3 3-3 17 0 20" fill="none" stroke="var(--cream)" stroke-width="1.4"/></svg>
        rowan@tbk-plumbing.com.au
      </li>
    </ul>

    <div class="abn">ABN - 73 215 904 386</div>
  </section>
</body>
</html>
```